Professional Business Card - TWO SIDES

I need a new business card design to be used by myself and my employees. I would like a professional card and for the front I thought I would like a dark blue thatch with our logo in a raised gold foil on top of it. On the other side I would like name, position, and contact info. I've uploaded our old design for an example of the info used.

Target Market(s)

Business Clients

Industry/Entity Type

CPA Firm

Contact Information for Business Card

Logo, Name, Title, Address, Phone Numbers, Website address, Email Address

Font styles to use
Serif
Sans Serif

Colors
0054AA
0677BA
7BADD7
CADEEF
E8F1F8
0094D4
00A9DD
6FCCEA
C7EBF8
E9F6FB

Requirements
Must have
• Modern Professional Look
Nice to have
• Logo in Gold Foil or ability to have is raised. I like our logo in a single color
Should not have
• I've uploaded old business card

```html
<!DOCTYPE html>
<html lang="en">
<head>
<meta charset="utf-8">
<title>Hale &amp; Hale Accounting — Business Card</title>
<link href="https://fonts.googleapis.com/css2?family=Arimo:wght@400;700&display=swap" rel="stylesheet">
<style>
  :root {
    --navy: #0c2f63;
    --navy-deep: #082552;
    --lime: #a6cf2c;
    --white: #ffffff;
    --ink: #123a70;
    --stage: #e9edf2;
  }
  * { margin: 0; padding: 0; box-sizing: border-box; }
  html, body { width: 1200px; height: 900px; overflow: hidden; }
  body {
    background: var(--stage);
    font-family: "Arimo", Arial, sans-serif;
    position: relative;
  }
  .card {
    position: absolute;
    width: 600px;
    height: 343px;
    border-radius: 22px;
    overflow: hidden;
    box-shadow: 0 10px 28px rgba(8, 37, 82, 0.22);
  }
  .card-front {
    left: 80px; top: 80px;
    background: linear-gradient(135deg, var(--navy-deep) 0%, var(--navy) 100%);
    display: flex; align-items: center; justify-content: center;
  }
  .brand-name {
    font-weight: 700;
    letter-spacing: 1px;
    text-transform: uppercase;
    line-height: 1.1;
  }
  .card-front .brand-name { color: var(--white); font-size: 38px; text-align: center; }
  .card-back { left: 520px; top: 477px; background: var(--white); }
  .card-back .wave { position: absolute; inset: 0; width: 100%; height: 100%; }
  .card-back .brand-name {
    position: absolute; left: 40px; top: 84px;
    width: 240px;
    color: var(--navy); font-size: 26px;
  }
  .divider {
    position: absolute; left: 300px; top: 30px;
    width: 2px; height: 170px; background: var(--navy);
  }
  .contact { position: absolute; left: 320px; top: 28px; color: var(--ink); }
  .contact .person { color: var(--lime); font-weight: 700; font-size: 21px; line-height: 1.2; }
  .contact .role { font-size: 14px; margin-top: 2px; }
  .contact .address { font-size: 14px; margin-top: 10px; line-height: 1.3; padding-left: 14px; }
  .contact ul { list-style: none; margin-top: 10px; font-size: 14px; }
  .contact li { display: flex; align-items: center; gap: 10px; margin-bottom: 4px; line-height: 1.25; }
  .contact li svg { width: 13px; height: 13px; flex: none; }
</style>
</head>
<body>
  <section class="card card-front" aria-label="Card front">
    <span class="brand-name">Hale &amp; Hale<br>Accounting</span>
  </section>

  <section class="card card-back" aria-label="Card back">
    <svg class="wave" viewBox="0 0 600 343" preserveAspectRatio="none" aria-hidden="true">
      <path d="M0,300 C150,332 300,300 420,252 C500,224 560,210 600,205 L600,343 L0,343 Z" fill="var(--navy)"/>
      <path d="M0,276 C160,318 300,286 410,222 C310,294 160,308 0,290 Z" fill="var(--lime)"/>
    </svg>
    <span class="brand-name">Hale &amp; Hale<br>Accounting</span>
    <div class="divider"></div>
    <div class="contact">
      <div class="person">Daniel Hart</div>
      <div class="role">Manager</div>
      <div class="address">Your address, city<br>state, ZIP 0000</div>
      <ul>
        <li>
          <svg viewBox="0 0 24 24"><path d="M6 2l4 4-2 3c1.5 3 4 5.5 7 7l3-2 4 4-3 4C10 21 3 14 2 5z" fill="var(--lime)"/></svg>
          555-014-2100
        </li>
        <li>
          <svg viewBox="0 0 24 24"><rect x="2" y="5" width="20" height="14" rx="2" fill="none" stroke="var(--lime)" stroke-width="2"/><path d="M2 6l10 7 10-7" fill="none" stroke="var(--lime)" stroke-width="2"/></svg>
          daniel@halehale.example
        </li>
        <li>
          <svg viewBox="0 0 24 24"><circle cx="12" cy="12" r="10" fill="var(--lime)"/><path d="M2 12h20M12 2c-4 5-4 15 0 20M12 2c4 5 4 15 0 20" stroke="var(--white)" stroke-width="1.5" fill="none"/></svg>
          www.halehale.example
        </li>
      </ul>
    </div>
  </section>
</body>
</html>
```